Detail Shop Business card design

i need a business card design for my new detailing company called 'Brisk's Polish Works'. i want an all black and white design . simple, direct and to the point. i want the designer to choose a fitting font to match the logothe front should have logo, address, phone and email and the back side should have a slogan and text indicating that we offer services on anything including cars, trucks, motorcycles and RVs. slogan will read "we take pride in your ride"
maybe also very small on the back side the IG icon with Brisks_Polish_Works

phone 208.417.6352
address 3847 E Larkin Ave
Spokane WA 99214
email: BrisksPolish@mailvexo.com

Target Market(s)

all ages , auto enthusiasts

Industry/Entity Type

Automotive

Contact Information for Business Card

the front should have logo, address, phone and email and the back side should have a slogan and text indicating that we offer services on anything including cars, trucks, motorcycles and RVs. slogan will read "we take pride in your ride"

phone 208.417.6352
address 3847 E Larkin Ave
Spokane WA 99214

Colors
000000
ffffff

Requirements
Must have
• bold font and very simple design with good spacing
Nice to have
• anything creative from the designer indicating we service any types of vehicles
Should not have
• any colors ,

```html
<!DOCTYPE html>
<html lang="en">
<head>
<meta charset="utf-8">
<title>Brisk's Polish Works – Business Card</title>
<link href="https://fonts.googleapis.com/css2?family=Roboto:wght@400;700&family=Oswald:wght@500;700&display=swap" rel="stylesheet">
<style>
  :root {
    --ink: #111111;
    --ink-soft: #555555;
    --paper: #ffffff;
    --backdrop: #e6e6e6;
    --shade: #2a2a2a;
  }
  * { box-sizing: border-box; margin: 0; padding: 0; }
  html, body { width: 1200px; height: 950px; overflow: hidden; }
  body { background: var(--backdrop); position: relative; font-family: "Roboto", Arial, sans-serif; color: var(--ink); }

  .card { position: absolute; background: var(--paper); box-shadow: 0 6px 18px rgba(0,0,0,0.18); overflow: hidden; }

  /* Front: vertical contact card */
  .card-front { left: 110px; top: 170px; width: 350px; height: 610px; }
  .contact { position: absolute; top: 70px; left: 0; right: 0; text-align: center; }
  .star { display: block; margin: 0 auto; fill: var(--ink); }
  .person-name { margin-top: 16px; font-weight: 700; font-size: 21px; letter-spacing: 1px; }
  .person-role { font-size: 15px; color: var(--ink-soft); letter-spacing: 0.5px; margin-top: 2px; }
  .address { margin-top: 20px; font-size: 14px; line-height: 1.45; color: var(--ink-soft); }
  .lines { margin-top: 16px; font-size: 14px; line-height: 1.5; color: var(--ink-soft); }
  .stars-pair { display: flex; justify-content: center; gap: 6px; margin-top: 18px; }
  .vehicle-art { position: absolute; left: 0; right: 0; bottom: 0; height: 230px;
    background: linear-gradient(180deg, var(--paper) 0%, #bdbdbd 30%, var(--shade) 62%, var(--ink) 100%); }

  /* Back: horizontal slogan card */
  .card-back { left: 540px; top: 300px; width: 580px; height: 345px; }
  .brand { position: absolute; top: 60px; left: 0; right: 0; display: flex; align-items: center; justify-content: center; gap: 16px; }
  .brand-dot { width: 34px; height: 34px; border-radius: 50%; background: var(--ink); }
  .brand-name { font-family: "Oswald", "Arial Narrow", sans-serif; font-weight: 700; font-size: 40px; letter-spacing: 1px; color: var(--ink); }
  .slogan { position: absolute; left: 70px; right: 70px; top: 205px; text-align: center;
    font-family: "Oswald", "Arial Narrow", sans-serif; font-weight: 700; font-size: 24px; letter-spacing: 1.5px; text-transform: uppercase;
    padding-bottom: 8px; border-bottom: 2px solid var(--ink); }
  .services { position: absolute; left: 0; right: 0; top: 262px; text-align: center;
    font-family: "Oswald", "Arial Narrow", sans-serif; font-weight: 500; font-size: 16px; letter-spacing: 0.5px; color: var(--ink); }
</style>
</head>
<body>
  <section class="card card-front">
    <div class="contact">
      <svg class="star" width="20" height="20" viewBox="0 0 24 24"><path d="M12 1l3.2 7.2 7.8.7-5.9 5.2 1.8 7.7L12 17.8 5.1 21.8l1.8-7.7L1 8.9l7.8-.7z"/></svg>
      <h1 class="person-name">DALE HARMON</h1>
      <p class="person-role">CEO/FOUNDER</p>
      <p class="address">3847 E Larkin Ave<br>Spokane WA 99214</p>
      <p class="lines">(P) 208.417.6352<br>(M) 836 215 7740<br>BrisksPolish@mailvexo.com<br>www.briskspolish.com</p>
      <div class="stars-pair">
        <svg class="star" width="16" height="16" viewBox="0 0 24 24"><path d="M12 1l3.2 7.2 7.8.7-5.9 5.2 1.8 7.7L12 17.8 5.1 21.8l1.8-7.7L1 8.9l7.8-.7z"/></svg>
        <svg class="star" width="16" height="16" viewBox="0 0 24 24"><path d="M12 1l3.2 7.2 7.8.7-5.9 5.2 1.8 7.7L12 17.8 5.1 21.8l1.8-7.7L1 8.9l7.8-.7z"/></svg>
      </div>
    </div>
    <div class="vehicle-art" role="img" aria-label="Black and white illustration of a classic hot rod car in side view"></div>
  </section>

  <section class="card card-back">
    <div class="brand">
      <span class="brand-dot"></span>
      <span class="brand-name">Brisk's Polish Works</span>
    </div>
    <p class="slogan">We take pride in your ride</p>
    <p class="services">Services on anything including cars, trucks, motorcycles &amp; RVs</p>
  </section>
</body>
</html>
```